Los Brava Dip – CPG Website with WordPress - Store Locator: WP Maps plugin

Larkfield Food Company is a startup consumer packaged goods (CPG) brand launching its flagship product line — Los Brava Dip. We’re seeking a talented web designer to create a bold, professional, mobile-optimized website using WordPress with a WP Maps store locator to help customers find local retailers.

Our goal is to build a strong online presence that supports both retail growth and direct-to-consumer sales.

See Los Brava _Website_Design_Brief word document.

The website URL is https://losbravadip.example/

Target Market(s)

Consumers of gourmet salsa

Industry/Entity Type

Consumer Packaged Goods - Salsa manufacturer.

Coding

Coded - Design and coding required

Number of Pages Required

5+ page

Requirements
Must have
• The design of the Los Brava Dip website shall emulate the clean, polished aesthetic of Fennigo.example.

```html
<!DOCTYPE html>
<html lang="en">
<head>
<meta charset="utf-8">
<title>Los Brava Dip</title>
<link href="https://fonts.googleapis.com/css2?family=Roboto+Condensed:wght@700&family=League+Spartan:wght@400;500;600;700&display=swap" rel="stylesheet">
<style>
:root{
  --red:#c8202b;
  --yellow-card:#f0b636;
  --red-card:#d1462a;
  --green-card:#3a7a2a;
  --green-btn:#2f6b22;
  --ink:#231a14;
  --review-bg:#22150a;
  --text:#2a2a2a;
  --muted:#666;
  --white:#fff;
  --line:#d9d9d9;
}
*{box-sizing:border-box;margin:0;padding:0}
html,body{width:1200px;height:3055px;overflow:hidden;background:var(--white)}
body{position:relative;font-family:"League Spartan",sans-serif;color:var(--text)}
.abs{position:absolute}
.display{font-family:"Roboto Condensed",sans-serif;font-weight:700;text-transform:uppercase}

/* header */
.site-header{position:absolute;left:0;top:0;width:1200px;height:80px;background:var(--white);z-index:5}
.brand-name{font-family:"Roboto Condensed",sans-serif;font-weight:700;color:var(--red);font-size:38px;line-height:1;white-space:nowrap}
.header-brand{position:absolute;left:112px;top:22px}
.main-nav a{position:absolute;top:34px;font-size:14px;font-weight:600;letter-spacing:1.2px;color:var(--ink);text-decoration:none}
.main-nav a.active{border-bottom:2px solid var(--red);padding-bottom:5px}
.btn-contact{position:absolute;left:951px;top:25px;width:130px;height:34px;border-radius:17px;background:var(--red);color:var(--white);font-size:14px;font-weight:600;letter-spacing:1.2px;display:flex;align-items:center;justify-content:center}

/* hero */
.hero{position:absolute;left:0;top:80px;width:1200px;height:590px;overflow:hidden;background:linear-gradient(100deg,#f4a62a 0%,#ee8a1a 45%,#d5541a 75%,#8f1e12 100%)}
.hero-title{position:absolute;left:0;width:1200px;text-align:center;color:var(--white)}
.hero-title .l1{position:absolute;left:285px;top:70px;width:622px;font-size:62px;line-height:64px;border-top:2px solid #fff;border-bottom:2px solid #fff}
.hero-title .l2{position:absolute;left:0;top:142px;width:1180px;font-size:58px;line-height:60px}
.hero-jars{position:absolute;left:278px;top:310px;width:630px;height:412px;border-radius:40px 40px 60px 60px;background:linear-gradient(90deg,#d83a2a 0%,#e25d2e 25%,#9fbd45 35%,#8cb23c 62%,#f08a23 72%,#e9462b 100%);z-index:3}

.eyebrow{font-size:16px;font-weight:600;letter-spacing:2px;color:var(--red);text-transform:uppercase}
.eyebrow.line{border-top:1px solid var(--red);padding-top:4px}
.sec-title{font-size:37px;color:var(--ink);line-height:1}
.swoosh{position:absolute}

/* product cards */
.product-card{position:absolute;top:900px;width:328px;height:378px;border-radius:6px}
.product-card .frame{position:absolute;inset:10px;border:2px solid rgba(255,255,255,.6);border-radius:4px}
.tag{position:absolute;left:50%;transform:translateX(-50%);top:40px;background:#111;color:#fff;font-size:16px;font-weight:600;letter-spacing:2px;padding:5px 22px 2px;white-space:nowrap}
.product-card p{position:absolute;left:10px;right:10px;top:82px;text-align:center;color:#fff;font-size:21px;font-weight:600;line-height:27px;white-space:nowrap}
.jar{position:absolute;left:88px;top:162px;width:156px;height:258px;border-radius:20px 20px 34px 34px}
.yellow{background:var(--yellow-card)}
.red{background:var(--red-card)}
.green{background:var(--green-card)}

/* reviews */
.reviews{position:absolute;left:0;top:1393px;width:1200px;height:521px;background:linear-gradient(180deg,#f0b534 0%,#eea12a 60%,#e88c20 100%)}
.review-card{position:absolute;top:230px;width:315px;height:175px;background:var(--review-bg);padding:38px 38px 0;color:#fff;font-size:17px;font-weight:600;line-height:23px}
.stars{display:flex;gap:5px;margin-bottom:18px}
.arrow{position:absolute;top:433px}

/* recipes */
.recipe-card{position:absolute;top:2080px;width:326px;height:406px;border:1px solid #bdbdbd;background:#fff}
.recipe-photo{height:232px}
.recipe-card h3{position:absolute;left:26px;top:252px;width:270px;font-size:20px;font-weight:600;line-height:19px;color:var(--ink)}
.recipe-card .desc{position:absolute;left:26px;top:298px;width:280px;font-size:13.5px;line-height:17px;color:var(--muted)}
.read-more{position:absolute;left:26px;top:346px;width:127px;height:34px;background:var(--green-btn);color:#fff;font-size:12px;font-weight:600;letter-spacing:1.2px;display:flex;align-items:center;justify-content:center}

/* follow */
.follow{position:absolute;left:0;top:2585px;width:1200px;height:275px;background:linear-gradient(100deg,#d23a1f 0%,#d3321f 50%,#a61b1e 100%)}
.follow h2{position:absolute;left:398px;top:56px;width:406px;border-top:1px solid rgba(255,255,255,.7);border-bottom:1px solid rgba(255,255,255,.7);text-align:center;color:#fff;font-size:30px;font-weight:700;letter-spacing:1px;padding:14px 0 6px}
.social{position:absolute;top:140px;width:80px;height:80px;border:3px solid #fff;border-radius:50%;color:#fff;font-size:12px;font-weight:600;display:flex;align-items:center;justify-content:center}

/* footer */
.site-footer{position:absolute;left:0;top:2860px;width:1200px;height:195px;background:#fff}
.footer-divider-v{position:absolute;left:294px;top:0;width:1px;height:195px;background:var(--line)}
.footer-nav a{position:absolute;top:70px;font-size:14px;font-weight:500;letter-spacing:1.2px;color:var(--ink);text-decoration:none}
.dot{position:absolute;top:75px;width:5px;height:5px;background:var(--red)}
.footer-divider-h{position:absolute;left:295px;top:115px;width:890px;height:1px;background:var(--line)}
.footer-small{position:absolute;top:150px;font-size:13px;color:var(--ink)}
.mini-social{position:absolute;top:144px;width:26px;height:26px;border-radius:50%;background:#111}
</style>
</head>
<body>

<header class="site-header">
  <div class="header-brand"><span class="brand-name">Los Brava</span></div>
  <nav class="main-nav">
    <a class="active" style="left:326px">ABOUT</a>
    <a style="left:431px">PRODUCTS</a>
    <a style="left:566px">WHERE TO BUY</a>
    <a style="left:735px">RECIPES</a>
    <a style="left:851px">REVIEWS</a>
  </nav>
  <div class="btn-contact">CONTACT ›</div>
</header>

<section class="hero" role="img" aria-label="Warm orange and red background with abstract curved shapes">
  <div class="hero-title display">
    <div class="l1">Spice up your meals!</div>
    <div class="l2">With Los Brava</div>
  </div>
  <svg class="abs" style="left:520px;top:198px" width="270" height="16" aria-hidden="true"><path d="M5 12 Q120 0 265 6" stroke="#fff" stroke-width="4" fill="none" stroke-linecap="round"/></svg>
</section>
<div class="hero-jars" role="img" aria-label="Three jars of Los Brava salsa: habanero, verde and all natural"></div>

<div class="abs eyebrow line" style="left:503px;top:790px">All Natural Salsa</div>
<h2 class="abs display sec-title" style="left:441px;top:818px">Featured Product</h2>
<svg class="swoosh" style="left:512px;top:860px" width="185" height="14" aria-hidden="true"><path d="M3 11 Q90 0 182 4" stroke="#c8202b" stroke-width="3.5" fill="none" stroke-linecap="round"/></svg>

<article class="product-card yellow" style="left:100px">
  <div class="frame"></div>
  <span class="tag">ALL NATURAL</span>
  <p>Bold, fresh, vibrant<br>flavor—no shortcuts.</p>
  <div class="jar" role="img" aria-label="Jar of all natural salsa" style="background:linear-gradient(180deg,#d7b04a 0%,#e1522a 20%,#e89a2a 60%,#d34a24 100%)"></div>
</article>
<article class="product-card red" style="left:442px">
  <div class="frame"></div>
  <span class="tag">HABANERO</span>
  <p>Fiery, intense, flavor-packed<br>pepper punch</p>
  <div class="jar" role="img" aria-label="Jar of habanero salsa" style="background:linear-gradient(180deg,#d7b04a 0%,#d93226 20%,#e0432a 60%,#c23a20 100%)"></div>
</article>
<article class="product-card green" style="left:782px">
  <div class="frame"></div>
  <span class="tag">VERDE</span>
  <p>Zesty, tangy, green heat<br>with balance</p>
  <div class="jar" role="img" aria-label="Jar of verde salsa" style="background:linear-gradient(180deg,#d7b04a 0%,#9cbf4a 20%,#aac24a 60%,#8ea63a 100%)"></div>
</article>

<section class="reviews">
  <div class="abs eyebrow line" style="left:510px;top:63px;color:#fff;border-color:#fff">What People Say</div>
  <h2 class="abs display sec-title" style="left:435px;top:93px;color:#fff">Customer Reviews</h2>
  <svg class="swoosh" style="left:508px;top:134px" width="185" height="14" aria-hidden="true"><path d="M3 11 Q90 0 182 4" stroke="#c8202b" stroke-width="3.5" fill="none" stroke-linecap="round"/></svg>
  <div class="abs" style="left:494px;top:170px;display:flex;align-items:center;gap:6px;color:#fff;font-size:13px;font-weight:600">
    <svg width="100" height="16" aria-hidden="true"><g fill="#fff"><polygon id="st" points="8,0 10,5.5 16,6 11.5,9.8 13,16 8,12.6 3,16 4.5,9.8 0,6 6,5.5"/><use href="#st" x="21"/><use href="#st" x="42"/><use href="#st" x="63"/><use href="#st" x="84"/></g></svg>
    <span>4.2 from 38 Reviews</span>
  </div>
  <div class="review-card" style="left:112px">
    <div class="stars"><svg width="100" height="16" aria-hidden="true"><g fill="#f2a024"><use href="#st"/><use href="#st" x="21"/><use href="#st" x="42"/><use href="#st" x="63"/><use href="#st" x="84"/></g></svg></div>
    “Overall, I very much enjoyed the salsa. Not too hot, but just righ”
  </div>
  <div class="review-card" style="left:446px">
    <div class="stars"><svg width="100" height="16" aria-hidden="true"><g fill="#f2a024"><use href="#st"/><use href="#st" x="21"/><use href="#st" x="42"/><use href="#st" x="63"/><use href="#st" x="84"/></g></svg></div>
    “Well priced. Love the heat...”
  </div>
  <div class="review-card" style="left:777px;top:228px">
    <div class="stars"><svg width="100" height="16" aria-hidden="true"><g fill="#f2a024"><use href="#st"/><use href="#st" x="21"/><use href="#st" x="42"/><use href="#st" x="63"/><use href="#st" x="84"/></g></svg></div>
    “Very good, and I'm a salsa snob!”
  </div>
  <svg class="arrow" style="left:570px" width="20" height="38" aria-hidden="true"><path d="M17 2 L3 19 L17 36" stroke="#fff" stroke-width="2.5" fill="none"/></svg>
  <svg class="arrow" style="left:620px" width="20" height="38" aria-hidden="true"><path d="M3 2 L17 19 L3 36" stroke="#fff" stroke-width="2.5" fill="none"/></svg>
</section>

<div class="abs eyebrow line" style="left:101px;top:1964px">Check Our Recipes</div>
<h2 class="abs display sec-title" style="left:97px;top:1996px">Featured Recipes</h2>
<svg class="swoosh" style="left:103px;top:2036px" width="185" height="14" aria-hidden="true"><path d="M3 11 Q90 0 182 4" stroke="#c8202b" stroke-width="3.5" fill="none" stroke-linecap="round"/></svg>

<article class="recipe-card" style="left:93px">
  <div class="recipe-photo" role="img" aria-label="Baked chicken with salsa and sour cream on a blue plate" style="background:linear-gradient(160deg,#e3a852 0%,#c98a4a 50%,#2a3f7a 100%)"></div>
  <h3>Baked Chicken with Salsa<br>and Sour Cream</h3>
  <p class="desc">Looking for a quick, hearty dish that<br>doesn't skimp on flavor?</p>
  <div class="read-more">READ MORE ›</div>
</article>
<article class="recipe-card" style="left:434px">
  <div class="recipe-photo" role="img" aria-label="Spoonful of one pot Mexican beef and rice with melted cheese" style="background:linear-gradient(160deg,#e8e2d8 0%,#c0602a 50%,#9c3e1a 100%)"></div>
  <h3>One Pot Mexican<br>Beef and Rice</h3>
  <p class="desc">This One Pot Mexican Beef and Rice is the ultimate weeknight dinner—quick to prepare</p>
  <div class="read-more">READ MORE ›</div>
</article>
<article class="recipe-card" style="left:777px">
  <div class="recipe-photo" role="img" aria-label="Bowls of black bean and salsa soup with fresh cilantro" style="background:linear-gradient(160deg,#6a4a54 0%,#7a5560 50%,#3a9aa8 100%)"></div>
  <h3>Los Brava's Black Bean<br>and Salsa Soup</h3>
  <p class="desc">Looking for a quick, hearty dish that doesn't skimp on flavor? Our Black Bean and Salsa</p>
  <div class="read-more">READ MORE ›</div>
</article>

<section class="follow">
  <h2>FOLLOW US ON</h2>
  <div class="social" style="left:507px">Circlebook</div>
  <div class="social" style="left:611px">Pixgram</div>
</section>

<footer class="site-footer">
  <div class="abs" style="left:70px;top:60px"><span class="brand-name" style="font-size:44px">Los Brava</span></div>
  <div class="footer-divider-v"></div>
  <nav class="footer-nav">
    <a style="left:348px">ABOUT</a><span class="dot" style="left:420px"></span>
    <a style="left:453px">PRODUCTS</a><span class="dot" style="left:558px"></span>
    <a style="left:589px">WHERE TO BUY</a><span class="dot" style="left:727px"></span>
    <a style="left:758px">RECIPES</a><span class="dot" style="left:844px"></span>
    <a style="left:872px">REVIEWS</a><span class="dot" style="left:962px"></span>
    <a style="left:993px">CONTACT</a>
  </nav>
  <div class="footer-divider-h"></div>
  <p class="footer-small" style="left:344px">© 2025 Larkfield Food Company. All rights reserved.</p>
  <span class="mini-social" style="left:790px"></span>
  <span class="mini-social" style="left:824px"></span>
  <p class="footer-small" style="left:878px">Privacy Policy</p>
  <p class="footer-small" style="left:975px">Terms of Use</p>
</footer>

</body>
</html>
```